Harbor Crestline (Business Card Design)

Need business cards designed. Something modern, chic, and sleek. Mabye the back of the card should be the navy blue that is in the logo and then just the logo on the back.

Target Market(s)

Those in the hotel, office, and renovation industry

Contact Information for Business Card

1. Logo 2. Dorian Fenwick 3. CEO/Founder 4. Phone: (833) HarbCre / (833) 427-2731 5. Email: dorian@theharborcrestline.com 6. Website: www.theharborcrestline.com

Font styles to use
Other font styles liked:
• Look at the logo font and base the font for everything else off of that.

Colors
0054AA
0677BA
7BADD7
CADEEF
E8F1F8

Requirements
Must have
• Colors that are associated in the logo
Nice to have
• Sleek modern clean and chic design.

```html
<!DOCTYPE html>
<html lang="en">
<head>
<meta charset="utf-8">
<title>Harbor Crestline — Business Cards</title>
<link href="https://fonts.googleapis.com/css2?family=Jost:wght@400;500;600&display=swap" rel="stylesheet">
<style>
  :root {
    --navy: #141a4b;
    --navy-deep: #070a24;
    --gold: #c9a247;
    --ink-grey: #555a66;
    --rule: #b9bcc4;
    --paper: #ffffff;
    --backdrop: #e4e5e8;
  }
  * { margin: 0; padding: 0; box-sizing: border-box; }
  html, body {
    width: 1200px; height: 800px; overflow: hidden;
    background: var(--backdrop);
    font-family: "Jost", sans-serif;
  }
  .sheet {
    position: relative; width: 1200px; height: 800px;
    display: flex; align-items: center; justify-content: center; gap: 40px;
  }
  .card {
    position: relative; width: 540px; height: 309px;
    box-shadow: 0 10px 30px rgba(20, 26, 75, 0.18);
  }
  /* Back side */
  .card--back {
    background: linear-gradient(135deg, var(--navy) 0%, var(--navy-deep) 100%);
  }
  .wordmark {
    position: absolute; display: flex; align-items: center; gap: 12px;
    font-weight: 600; letter-spacing: 0.14em; text-transform: uppercase;
    font-size: 24px; line-height: 1;
  }
  .wordmark__mark { width: 12px; height: 12px; background: var(--gold); flex: none; }
  .card--back .wordmark { right: 40px; bottom: 44px; color: var(--paper); }
  /* Front side */
  .card--front { background: var(--paper); }
  .card--front .wordmark { right: 36px; top: 150px; color: var(--navy); font-size: 20px; }
  .contact { position: absolute; left: 34px; top: 56px; width: 470px; }
  .contact__name {
    font-weight: 600; font-size: 17px; color: var(--navy);
    letter-spacing: 0.02em; text-transform: uppercase;
  }
  .contact__title { font-weight: 400; color: var(--ink-grey); text-transform: none; letter-spacing: 0; }
  .contact__title::before { content: "|"; color: var(--navy); margin: 0 8px; font-weight: 600; }
  .contact__line {
    display: flex; align-items: center; gap: 7px; margin-top: 7px;
    font-size: 13px; color: var(--ink-grey);
  }
  .contact__line svg { width: 12px; height: 12px; flex: none; }
  .contact__sep { color: var(--gold); margin: 0 4px; }
  .accent { color: var(--gold); }
  .contact__rule {
    position: absolute; left: 34px; right: 36px; top: 232px;
    border-top: 1px solid var(--rule);
  }
  .contact__web {
    position: absolute; left: 34px; right: 36px; top: 248px;
    display: flex; justify-content: flex-end; align-items: center; gap: 7px;
    font-size: 13px; color: var(--ink-grey);
  }
  .contact__web svg { width: 12px; height: 12px; }
</style>
</head>
<body>
<main class="sheet">
  <section class="card card--back" aria-label="Card back">
    <div class="wordmark"><span class="wordmark__mark"></span>Harbor Crestline</div>
  </section>

  <section class="card card--front" aria-label="Card front">
    <div class="contact">
      <p class="contact__name">Dorian Fenwick<span class="contact__title">CEO/Founder</span></p>
      <p class="contact__line">
        <svg viewBox="0 0 12 12" aria-hidden="true"><path fill="#c9a247" d="M2.5 1h2l1 2.5-1.3 1a6 6 0 0 0 3.3 3.3l1-1.3L11 7.5v2A1.5 1.5 0 0 1 9.5 11 8.5 8.5 0 0 1 1 2.5 1.5 1.5 0 0 1 2.5 1z"/></svg>
        (833) HarbCre<span class="contact__sep">/</span>(833) 427-2731
      </p>
      <p class="contact__line">
        <svg viewBox="0 0 12 12" aria-hidden="true"><rect x="1" y="2.5" width="10" height="7" rx="1" fill="#c9a247"/><path d="M1.5 3l4.5 3.5L10.5 3" stroke="#fff" stroke-width="1" fill="none"/></svg>
        dorian@<span class="accent">theharborcrestline</span>.com
      </p>
    </div>
    <div class="wordmark"><span class="wordmark__mark"></span>Harbor Crestline</div>
    <div class="contact__rule"></div>
    <p class="contact__web">
      <svg viewBox="0 0 12 12" aria-hidden="true"><circle cx="6" cy="6" r="5" fill="none" stroke="#c9a247" stroke-width="1.2"/><path d="M1 6h10M6 1c-2 2.5-2 7.5 0 10M6 1c2 2.5 2 7.5 0 10" fill="none" stroke="#c9a247" stroke-width="0.9"/></svg>
      www.<span class="accent">theharborcrestline</span>.com
    </p>
  </section>
</main>
</body>
</html>
```